Velk Partners Building Business Cards

We need a business card that reflects our business as "Solar Experts" in San Diego. Browse our website www.velkpartners.example our License needs to be displayed as "CSLB# 3867140" our phone number is (619) 555-0187

Save thousands on your electric bills and increase the value of your home while helping to protect the environment. Our solar installation experts will help you design the system that's right for you, using only the highest quality equipment that will look great and give you ideal performance. Our goal is to make you energy independent, and get your electric bill to 0.

Paul Osterby
(619) 555-0187
paul@velkpartners.example

Target Market(s)

Home owners in san diego looking for solar

Industry/Entity Type

Solar Energy

Contact Information for Business Card

Paul Osterby
(619) 555-0187
paul@velkpartners.example

Font styles to use
Other font styles liked:
• Use our logo font

Requirements
Must have
• License needs to be displayed as "CSLB# 3867140" our phone number is (619) 555-0187
Nice to have
• Real images of rooftop home solar in san diego
Should not have
• our business address

```html
<!DOCTYPE html>
<html lang="en">
<head>
<meta charset="utf-8">
<title>Velk Partners Building – Business Cards</title>
<link rel="stylesheet" href="https://fonts.googleapis.com/css2?family=Lora:wght@400;700&display=swap">
<style>
  :root {
    --stage: #222222;
    --navy: #1f3d78;
    --navy-photo-light: #3a5590;
    --navy-photo-dark: #253f7a;
    --sun: #f7ae1f;
    --paper: #ffffff;
  }
  * { box-sizing: border-box; margin: 0; padding: 0; }
  html, body {
    width: 1189px; height: 1200px; overflow: hidden;
    background: var(--stage);
    font-family: "Lora", Georgia, serif;
  }
  .card {
    position: absolute;
    left: 171px;
    width: 856px;
    height: 487px;
    border-radius: 22px;
    overflow: hidden;
  }
  /* Front */
  .card--front { top: 68px; }
  .front__photo {
    position: absolute; inset: 0;
    background: linear-gradient(135deg, var(--navy-photo-light) 0%, var(--navy-photo-dark) 55%, var(--navy-photo-light) 100%);
  }
  .front__brand {
    position: absolute; left: 0; right: 0; top: 190px;
    text-align: center;
  }
  .brand-name {
    font-family: "Lora", Georgia, serif;
    font-weight: 700;
    letter-spacing: -0.5px;
    line-height: 1;
  }
  .front__brand .brand-name { color: var(--paper); font-size: 58px; }
  .social {
    position: absolute; top: 335px; left: 0; right: 0;
    display: flex; justify-content: center; gap: 19px;
  }
  .social__square {
    width: 35px; height: 35px; border-radius: 3px;
    background: var(--paper);
  }
  /* Back */
  .card--back { top: 626px; background: var(--paper); }
  .back__brand {
    position: absolute; left: 0; right: 0; top: 95px;
    text-align: center;
  }
  .back__brand .brand-name { color: var(--navy); font-size: 58px; }
  .name-band {
    position: absolute; left: 0; right: 0; top: 254px; height: 56px;
    background: var(--sun);
    display: flex; align-items: center; justify-content: center;
  }
  .name-band__name {
    color: var(--navy); font-weight: 700; font-size: 31px;
    letter-spacing: 0.5px; text-transform: uppercase;
  }
  .contact {
    position: absolute; left: 0; right: 0; top: 310px; bottom: 0;
    background: var(--navy);
    color: var(--paper);
    text-align: center;
    font-size: 24px;
    line-height: 31px;
    padding-top: 28px;
  }
  .contact__label, .contact__accent { color: var(--sun); }
  .contact__license { font-size: 22px; margin-top: 6px; }
</style>
</head>
<body>
  <section class="card card--front">
    <div class="front__photo" role="img" aria-label="Blue-tinted photo of rooftop solar panels"></div>
    <div class="front__brand"><span class="brand-name">Velk Partners Building</span></div>
    <div class="social" aria-label="Social media links">
      <span class="social__square"></span>
      <span class="social__square"></span>
      <span class="social__square"></span>
      <span class="social__square"></span>
    </div>
  </section>

  <section class="card card--back">
    <div class="back__brand"><span class="brand-name">Velk Partners Building</span></div>
    <div class="name-band"><h1 class="name-band__name">Paul Osterby</h1></div>
    <div class="contact">
      <p><span class="contact__label">Phone:</span> (619) 555-0187</p>
      <p><span class="contact__label">Email:</span> paul@velkpartners.example</p>
      <p>www.<span class="contact__accent">velkpartners</span>.example</p>
      <p class="contact__license">CSLB# 3867140</p>
    </div>
  </section>
</body>
</html>
```